Business card design

We need a business card designed completed for a new company. We are a company that works with associations, schools to convert their older text/DVDs into dynamic online and mobile programs. Our initial platform is designed for the legal associations and will enable their lawyers to access their content such as forms, videos, case law and support materials anywhere, anytime. We are also focused on Project Management Associations, Financial Management Associations and IT Associations.

I would like for the business card to have the following information:

Logo

Kent marrowby

President and CEO

kmarrowby@trevantiq.example

Mobile: 555-374-9160

www.trevantiq.example

Tag line: Transforming content into a mobile platform    

I would like it to be double sided, use the colours of the logo, tie into the mobile world

 

Industry/Entity Type

Legal

Logo Text

Trevantiq

```html
<!DOCTYPE html>
<html lang="en">
<head>
<meta charset="utf-8">
<title>Trevantiq business card set</title>
<link href="https://fonts.googleapis.com/css2?family=Open+Sans:wght@400;600;700&display=swap" rel="stylesheet">
<style>
  :root {
    --stage: #5e3d24;
    --label: #141414;
    --card-grey: #999999;
    --card-white: #ffffff;
    --ink-dark: #1c1c1c;
    --ink-mid: #5a5a5a;
    --wordmark-light: #ffffff;
    --wordmark-dark: #555555;
    --accent-dark: #7a7a7a;
    --accent-light: #d6d6d6;
  }
  * { margin: 0; padding: 0; box-sizing: border-box; }
  html, body {
    width: 1200px; height: 800px; overflow: hidden;
    background: var(--stage);
    font-family: "Open Sans", Arial, sans-serif;
  }
  .sheet { position: relative; width: 1200px; height: 800px; }
  .view-label {
    position: absolute; width: 510px; text-align: center;
    font-size: 21px; color: var(--label); font-weight: 400;
  }
  .card {
    position: absolute; width: 510px; height: 290px;
    border-radius: 20px; overflow: hidden;
    box-shadow: 0 4px 10px rgba(0,0,0,0.45);
    text-align: center;
  }
  .card--grey { background: var(--card-grey); }
  .card--white { background: var(--card-white); }
  .corner-accent { position: absolute; width: 110px; height: 44px; }
  .corner-accent--top {
    top: 0; right: 0;
    background: linear-gradient(200deg, var(--accent-dark) 0%, var(--accent-light) 45%, transparent 75%);
  }
  .corner-accent--bottom {
    bottom: 0; left: 0;
    background: linear-gradient(20deg, var(--accent-dark) 0%, var(--accent-light) 45%, transparent 75%);
  }
  .wordmark {
    position: absolute; left: 0; right: 0;
    font-weight: 700; letter-spacing: -0.5px; line-height: 1;
  }
  .card--grey .wordmark { color: var(--wordmark-light); }
  .card--white .wordmark { color: var(--wordmark-dark); }
  .wordmark--small { top: 46px; font-size: 54px; }
  .wordmark--large { top: 112px; font-size: 70px; }
  .holder { position: absolute; top: 143px; left: 0; right: 0; font-size: 12px; }
  .holder__name { font-weight: 700; font-size: 15px; }
  .card--grey .holder { color: var(--ink-dark); }
  .card--white .holder { color: var(--ink-mid); }
  .contact {
    position: absolute; top: 199px; left: 30px; right: 30px;
    font-size: 11px; color: var(--ink-dark); white-space: nowrap;
  }
  .contact b { font-style: italic; font-weight: 700; }
  .contact .sep { margin: 0 4px; }
  .tagline { position: absolute; top: 240px; left: 0; right: 0; font-size: 15px; }
  .card--grey .tagline { color: var(--wordmark-light); }
  .card--white .tagline { color: var(--ink-dark); }
  .site { position: absolute; top: 252px; left: 0; right: 0; font-size: 15px; letter-spacing: 3px; color: var(--ink-dark); }
</style>
</head>
<body>
<main class="sheet">
  <p class="view-label" style="left:73px; top:50px;">Front</p>
  <p class="view-label" style="left:639px; top:50px;">Back - 1</p>
  <p class="view-label" style="left:73px; top:410px;">Back - 2</p>
  <p class="view-label" style="left:634px; top:410px;">Back - 3</p>

  <section class="card card--grey" style="left:73px; top:97px;">
    <div class="corner-accent corner-accent--top" role="img" aria-label="Grey corner swoosh accent"></div>
    <div class="corner-accent corner-accent--bottom" role="img" aria-label="Grey corner swoosh accent"></div>
    <h1 class="wordmark wordmark--small">Trevantiq</h1>
    <p class="holder"><span class="holder__name">Kent marrowby,</span> President and CEO</p>
    <p class="contact"><b>C</b> : 555-374-9160<span class="sep">|</span><b>E</b> : kmarrowby@trevantiq.example<span class="sep">|</span><b>W</b> : www.trevantiq.example</p>
    <p class="tagline">Transforming content into a mobile platform</p>
  </section>

  <section class="card card--white" style="left:639px; top:97px;">
    <div class="corner-accent corner-accent--top" role="img" aria-label="Grey corner swoosh accent"></div>
    <div class="corner-accent corner-accent--bottom" role="img" aria-label="Grey corner swoosh accent"></div>
    <h2 class="wordmark wordmark--small">Trevantiq</h2>
    <p class="holder"><span class="holder__name">Kent marrowby,</span> President and CEO</p>
    <p class="contact"><b>C</b> : 555-374-9160<span class="sep">|</span><b>E</b> : kmarrowby@trevantiq.example<span class="sep">|</span><b>W</b> : www.trevantiq.example</p>
    <p class="tagline">Transforming content into a mobile platform</p>
  </section>

  <section class="card card--grey" style="left:73px; top:452px;">
    <h2 class="wordmark wordmark--large">Trevantiq</h2>
    <p class="site">www.trevantiq.example</p>
  </section>

  <section class="card card--white" style="left:634px; top:450px;">
    <h2 class="wordmark wordmark--large">Trevantiq</h2>
    <p class="site">www.trevantiq.example</p>
  </section>
</main>
</body>
</html>
```